Boutique custom software development company needs new business card

Our nearly 20 year old custom software development company would like to better include the fact that we are now providing Bitcoin services. These new services are B2B include education (how to acquire and securely hold Bitcoin) and integrating Bitcoin payments into existing ecommerce sites or other existing systems. Please keep the card clean and simple. Attached is our current design and some other files. vextorial.com

Target Market(s)

businesses owners interested in long term relationship

Industry/Entity Type

Custom software development and Bitcoin

Contact Information for Business Card

Dale Parker, dale@vextorial.com, vextorial.com, (888) 555-VXTRL

Font styles to use
Other font styles liked:
• monospace

Requirements
Must have
• double-sided
Nice to have
• clean and simple
Should not have
• physical address

```html
<!DOCTYPE html>
<html lang="en">
<head>
<meta charset="utf-8">
<title>Vextorial business card</title>
<link href="https://fonts.googleapis.com/css2?family=Montserrat:wght@400;500;800&display=swap" rel="stylesheet">
<style>
  :root {
    --backdrop: #2f3032;
    --card: #d9e2ee;
    --brand-blue: #3b72c1;
    --brand-orange: #f07f22;
    --ink: #3a3d44;
  }
  * { box-sizing: border-box; margin: 0; padding: 0; }
  html, body {
    width: 1200px; height: 801px; overflow: hidden;
    background: var(--backdrop);
    font-family: "Montserrat", sans-serif;
  }
  .canvas {
    width: 1200px; height: 801px;
    display: flex; align-items: center; justify-content: center; gap: 40px;
  }
  .card {
    position: relative;
    width: 540px; height: 309px;
    background: var(--card);
    border-radius: 14px;
    overflow: hidden;
  }
  /* front */
  .card-front { display: flex; align-items: center; justify-content: center; }
  .front-lockup { text-align: left; }
  .wordmark {
    font-weight: 800; font-size: 64px; line-height: 1;
    color: var(--brand-blue); letter-spacing: -1px;
  }
  .tagline {
    margin-top: 6px;
    font-weight: 400; font-size: 19px; color: var(--brand-blue);
    letter-spacing: -0.3px;
  }
  .services {
    margin-top: 14px;
    display: flex; align-items: center; gap: 8px;
    font-weight: 500; font-size: 14px; color: var(--brand-orange);
    letter-spacing: 0.2px;
  }
  .services .dot {
    width: 5px; height: 5px; border-radius: 50%; background: var(--brand-orange); flex: none;
  }
  /* back */
  .back-brand {
    position: absolute; top: 34px; right: 38px;
    display: flex; align-items: center; gap: 10px;
  }
  .back-brand .brand-square {
    width: 22px; height: 22px; background: var(--brand-orange);
  }
  .back-brand .brand-name {
    font-weight: 800; font-size: 28px; color: var(--brand-blue);
  }
  .person {
    position: absolute; left: 44px; top: 150px;
  }
  .person-name {
    font-weight: 800; font-size: 25px; letter-spacing: 0.5px; line-height: 1.05;
  }
  .person-name .first { color: var(--brand-orange); }
  .person-name .last { color: var(--brand-blue); }
  .person-title {
    font-weight: 400; font-size: 16px; color: var(--ink); margin-top: 2px;
  }
  .divider {
    position: absolute; left: 44px; right: 34px; top: 218px;
    height: 1.5px; background: var(--brand-orange);
  }
  .website {
    position: absolute; right: 34px; top: 192px;
  }
  .contacts {
    position: absolute; left: 44px; top: 232px;
    display: flex; flex-direction: column; gap: 8px;
  }
  .contact-line {
    display: flex; align-items: center; gap: 8px;
    font-weight: 400; font-size: 14.5px; color: var(--ink);
  }
  .website.contact-line { font-size: 12.5px; }
  .contact-line svg { width: 13px; height: 13px; fill: var(--brand-blue); flex: none; }
</style>
</head>
<body>
<main class="canvas">
  <section class="card card-front" aria-label="Card front">
    <div class="front-lockup">
      <div class="wordmark">Vextorial</div>
      <div class="tagline">developer of custom applications</div>
      <div class="services">
        <span>Bitcoin education</span><span class="dot"></span><span>Bitcoin payment integration</span>
      </div>
    </div>
  </section>

  <section class="card card-back" aria-label="Card back">
    <div class="back-brand">
      <span class="brand-square"></span>
      <span class="brand-name">Vextorial</span>
    </div>

    <div class="person">
      <div class="person-name"><span class="first">DALE</span> <span class="last">PARKER</span></div>
      <div class="person-title">Owner</div>
    </div>

    <div class="website contact-line">
      <svg viewBox="0 0 16 16" aria-hidden="true"><circle cx="8" cy="8" r="7" fill="none" stroke="#3b72c1" stroke-width="1.6"/><path d="M1 8h14M8 1c-3 3.5-3 10.5 0 14M8 1c3 3.5 3 10.5 0 14" fill="none" stroke="#3b72c1" stroke-width="1.2"/></svg>
      <span>www.vextorial.com</span>
    </div>

    <div class="divider"></div>

    <div class="contacts">
      <div class="contact-line">
        <svg viewBox="0 0 16 16" aria-hidden="true"><path d="M3.6 1.2l2.3 2.7-1.4 1.8c.9 2 2.4 3.5 4.4 4.4l1.8-1.4 2.7 2.3-1.3 2.2C7.2 14.9 1.1 8.8 1.4 2.5z"/></svg>
        <span>(888) 555-VXTRL</span>
      </div>
      <div class="contact-line">
        <svg viewBox="0 0 16 16" aria-hidden="true"><path d="M1 3h14v10H1z"/><path d="M1 3l7 6 7-6" fill="none" stroke="#d9e2ee" stroke-width="1.3"/></svg>
        <span>dale@vextorial.com</span>
      </div>
    </div>
  </section>
</main>
</body>
</html>
```